Road Construction Company needs business cards

We would like a new business card designed for our business.

We're a road construction company based in Qld, Australia.

Can the business card please have the following information on it.

Name: Warren Halbeck
Position: General Manager
Phone: 0472 915 348
Email: Warren.halbeck@tovrin.com.au
Address: 87 Marrow Ave, Pendlebay, QLD, 4023
Website: www.tovrin.com.au

Visually we'd like the card to be professional and simple.

Attached is our logo.

Our website is www.tovrin.com.au

Target Market(s)

Men aged 25-60

Contact Information for Business Card

As listed in project description

Font styles to use
Serif

Requirements
Must have
• Large logo on back of card

```html
<!DOCTYPE html>
<html lang="en">
<head>
<meta charset="utf-8">
<title>Tovrin Business Card</title>
<link rel="stylesheet" href="https://fonts.googleapis.com/css2?family=Lato:wght@400;700;900&display=swap">
<style>
  :root {
    --backdrop: #8e8e8e;
    --paper: #ffffff;
    --wash: #edf1f7;
    --navy: #0d55a8;
    --brand-blue: #0057a8;
    --sky: #2fa4dc;
    --ink: #1f2430;
    --cyan: #3cc4f2;
  }
  * { margin: 0; padding: 0; box-sizing: border-box; }
  html, body { width: 1200px; height: 800px; overflow: hidden; }
  body {
    background: var(--backdrop);
    font-family: "Lato", sans-serif;
    display: flex;
    align-items: center;
    justify-content: center;
    gap: 48px;
  }
  .card {
    position: relative;
    width: 540px;
    height: 330px;
    border-radius: 20px;
    overflow: hidden;
  }
  .card-front { background: var(--paper); }
  .front-wash { position: absolute; inset: 0; }
  .brand-name {
    font-family: "Lato", sans-serif;
    font-weight: 900;
    letter-spacing: 2px;
  }
  .front-brand {
    position: absolute;
    right: 40px;
    top: 38px;
    font-size: 54px;
    color: var(--navy);
  }
  .identity {
    position: absolute;
    left: 38px;
    top: 122px;
  }
  .person-name {
    font-weight: 900;
    font-size: 26px;
    color: var(--navy);
    text-transform: uppercase;
    letter-spacing: 0.5px;
  }
  .person-role {
    font-size: 19px;
    color: var(--sky);
    margin-top: 2px;
  }
  .divider {
    position: absolute;
    left: 38px;
    right: 40px;
    top: 196px;
    height: 1px;
    background: var(--sky);
  }
  .contact-list {
    position: absolute;
    left: 38px;
    top: 210px;
    list-style: none;
    font-size: 15px;
    color: var(--ink);
    line-height: 1.6;
  }
  .contact-list li { display: flex; align-items: center; gap: 9px; }
  .contact-icon { width: 13px; height: 13px; fill: var(--navy); flex: none; }
  .address {
    position: absolute;
    right: 40px;
    top: 214px;
    font-size: 15px;
    color: var(--ink);
    text-align: right;
    line-height: 1.45;
  }
  .front-band { position: absolute; left: 0; bottom: 0; width: 540px; height: 50px; }
  .website {
    position: absolute;
    right: 28px;
    bottom: 11px;
    font-size: 15px;
    color: var(--paper);
    letter-spacing: 3px;
  }
  .card-back {
    background: var(--brand-blue);
    display: flex;
    align-items: center;
    justify-content: center;
  }
  .back-brand {
    font-size: 92px;
    color: var(--cyan);
  }
</style>
</head>
<body>
  <section class="card card-front" aria-label="Business card front">
    <svg class="front-wash" viewBox="0 0 540 330" aria-hidden="true">
      <polygon points="0,200 250,150 540,215 540,330 0,330" fill="var(--wash)"/>
    </svg>
    <div class="front-brand brand-name">TOVRIN</div>
    <div class="identity">
      <div class="person-name">Warren Halbeck</div>
      <div class="person-role">General Manager</div>
    </div>
    <div class="divider"></div>
    <ul class="contact-list">
      <li>
        <svg class="contact-icon" viewBox="0 0 24 24" aria-hidden="true"><path d="M6.6 10.8a15.1 15.1 0 0 0 6.6 6.6l2.2-2.2a1 1 0 0 1 1-.25 11.4 11.4 0 0 0 3.6.57 1 1 0 0 1 1 1V20a1 1 0 0 1-1 1A17 17 0 0 1 3 4a1 1 0 0 1 1-1h3.5a1 1 0 0 1 1 1c0 1.25.2 2.45.57 3.6a1 1 0 0 1-.25 1z"/></svg>
        <span>0472 915 348</span>
      </li>
      <li>
        <svg class="contact-icon" viewBox="0 0 24 24" aria-hidden="true"><path d="M2 5h20v14H2z M3.5 6.5 12 13l8.5-6.5" stroke="#fff" stroke-width="1.5"/></svg>
        <span>Warren.halbeck@tovrin.com.au</span>
      </li>
    </ul>
    <address class="address" style="font-style:normal">87 Marrow Ave<br>Pendlebay, QLD, 4023</address>
    <svg class="front-band" viewBox="0 0 540 50" aria-hidden="true">
      <rect x="0" y="36" width="360" height="6" fill="var(--sky)"/>
      <path d="M0 42 H330 C348 42 350 36 352 26 C354 14 360 8 374 8 H540 V50 H0 Z" fill="var(--navy)"/>
    </svg>
    <div class="website">www.tovrin.com.au</div>
  </section>

  <section class="card card-back" aria-label="Business card back">
    <div class="back-brand brand-name">TOVRIN</div>
  </section>
</body>
</html>
```